Business Card Design

We custom build & and install Air filtration systems for mining machines - the system filters the air going into the cabin to protect the operator/driver Examples of the machines we install our units to would be Ironhaven or Veltoro. Australian owned company Our company colors are sky blue with polished Stainless steel lettering & framing. I have a logo which I will upload but I would like the new image to be crisper.

Industry/Entity Type

Business

Contact Information for Business Card

Company name - Clearlung Pty Ltd
Dale Morrissey - Position - Sales & Product Development Contact numbers Mob 0428 359 162 Tel - 07 3581 4296
Address - 147 Quarrel Rd, Wendlebury, Brisbane 4108, Australia

Colors
0255a3

Requirements
Must have
• sky blue & polished chrome lettering

```html
<!DOCTYPE html>
<html lang="en">
<head>
<meta charset="utf-8">
<title>Clearlung Business Card</title>
<link rel="stylesheet" href="https://fonts.googleapis.com/css2?family=Open+Sans:wght@400;600;700&display=swap">
<style>
  :root {
    --backdrop: #d9d7d3;
    --card: #e8e9ea;
    --brand-blue: #253f94;
    --ink: #2b2b2b;
    --on-blue: #ffffff;
  }
  * { margin: 0; padding: 0; box-sizing: border-box; }
  html, body {
    width: 1200px;
    height: 941px;
    overflow: hidden;
    background: var(--backdrop);
    font-family: "Open Sans", Arial, sans-serif;
  }
  .card {
    position: absolute;
    left: 356px;
    top: 70px;
    width: 489px;
    height: 800px;
    background: var(--card);
    border-radius: 34px;
    overflow: hidden;
  }
  .brand {
    position: absolute;
    left: 108px;
    top: 92px;
    display: flex;
    align-items: center;
    gap: 14px;
  }
  .brand-square {
    width: 30px;
    height: 30px;
    background: var(--brand-blue);
  }
  .brand-name {
    font-size: 54px;
    font-weight: 700;
    color: var(--brand-blue);
    line-height: 1;
    letter-spacing: 0.5px;
  }
  .rule {
    position: absolute;
    left: 0;
    width: 100%;
    height: 7px;
    background: var(--brand-blue);
  }
  .rule-top { top: 210px; }
  .rule-bottom { top: 388px; }
  .title-band {
    position: absolute;
    left: 0;
    top: 226px;
    width: 100%;
    height: 153px;
    background: var(--brand-blue);
    color: var(--on-blue);
    padding: 36px 0 0 108px;
  }
  .person-name {
    font-size: 34px;
    font-weight: 400;
    letter-spacing: 1px;
    line-height: 1.15;
  }
  .person-role {
    font-size: 26px;
    font-weight: 400;
    line-height: 1.3;
  }
  .contact-list {
    position: absolute;
    left: 108px;
    top: 430px;
    list-style: none;
    color: var(--ink);
    font-size: 21px;
    line-height: 1.45;
  }
</style>
</head>
<body>
  <div class="card">
    <div class="brand">
      <span class="brand-square"></span>
      <span class="brand-name">Clearlung</span>
    </div>
    <div class="rule rule-top"></div>
    <div class="title-band">
      <p class="person-name">ROWAN PRYCE</p>
      <p class="person-role">Managing Director</p>
    </div>
    <div class="rule rule-bottom"></div>
    <ul class="contact-list">
      <li>041.9th floor,Harbour Gate Road QLD</li>
      <li>013 472 5816</li>
      <li>myname@postbox.com</li>
      <li>mysitename.com</li>
    </ul>
  </div>
</body>
</html>
```